NEW Wordpress Website Design for a Dynamic Long Term Healthcare Company in Hawaii

I would like a new website design for my current company, Marlow Health Collective, which has two different brands - Marlow Homecare and Marlow Senior Living. You can see the current website at www.marlowhealth-example.com. The website should be built using Wordpress Software and the Framewise theme. The website should have a local Hawaii island/tropical feel, but look professional for healthcare. I'm looking for something fresh, and want the designer to select colors, styles, etc.

In the Header, on all pages, I would like a menu that includes Home Care, Senior Living, Rates, and About Us.
Under each of the Header Menu Titles, I would like these drop downs included:
Home Care (drop down pages)- Nurse Aide Care, 24-Hour Home Care, Skilled Nursing, Lifestyle Aide, Hospice at Home, Bathing & Meal Service.
Senior Living (drop down pages) - Long-Term Stay, Short-Term Stay.
Rates (drop down page) - Rates.
About Us (drop down pages) - Our Mission, Ohana Talk, About Dana Marlow.

In the footer, on all pages, you should include the address: 248 Pueo Lane, Suite 310, Honolulu, HI 96817. Phone number: 808-555-0172
The footer should also include buttons for a page called Learn, Caregiver Jobs, and each of the service page links to include: Nurse Aide Care, 24-Hour Home Care, Skilled Nursing, Lifestyle Aide, Hospice at Home, Bathing & Meal Service.
Please don't take the current website and redesign a few aspects. I'm looking for a completely different look and feel.

Target Market(s)

40-80 year olds

Industry/Entity Type

Long Term Healthcare

Coding

Coded - Design and coding required

Requirements
Should not have
• Our existing website as a template. We are looking for a complete redesign. Thank you.

```html
<!DOCTYPE html>
<html lang="en">
<head>
<meta charset="utf-8">
<title>Marlow Health Collective – Mobile Screens</title>
<link href="https://fonts.googleapis.com/css2?family=Roboto:wght@400;500;700&display=swap" rel="stylesheet">
<style>
:root{
  --teal:#5b9690;
  --teal-dark:#3f7c76;
  --teal-soft:#9cc6c1;
  --aqua:#bdf0ee;
  --ink:#141414;
  --muted:#555;
  --line:#d6d6d6;
  --panel:#ececec;
  --white:#fff;
  --photo-warm:#b48a5e;
  --photo-green:#6e8f4e;
}
*{box-sizing:border-box;margin:0;padding:0}
html,body{width:1200px;height:3841px;overflow:hidden;background:var(--white)}
body{font-family:"Roboto",Arial,sans-serif;color:var(--ink);position:relative}
.a{position:absolute}
.teal{color:var(--teal)}
.small{font-size:11.5px;line-height:22px;color:var(--muted)}
.label{font-size:12px;font-weight:500}
.btn{position:absolute;display:flex;align-items:center;justify-content:center;font-size:12px;border-radius:2px}
.btn-fill{background:var(--teal);color:var(--white)}
.btn-line{border:1.5px solid var(--teal);color:var(--teal);background:var(--white)}
.photo{position:absolute;background:linear-gradient(135deg,var(--photo-green),var(--photo-warm))}
.link{font-size:12px;color:var(--teal)}
.center{text-align:center}
h1,h2,h3{font-weight:500}

/* menu column */
.menu-item{position:absolute;left:18px;display:flex;align-items:center;gap:12px;font-size:12.5px;color:var(--teal)}
.menu-item svg{width:18px;height:18px}
.nav-row{position:absolute;left:18px;width:312px;display:flex;justify-content:space-between;font-size:14px;font-weight:500}
.product-panel{left:18px;top:434px;width:312px;height:398px;background:var(--panel)}
.brand-box{left:40px;top:499px;width:268px;height:172px;background:var(--white);display:flex;align-items:center;justify-content:center;font-size:28px;color:var(--ink)}

/* steps column */
.step-title{position:absolute;left:440px;width:312px;text-align:center;font-size:16px;font-weight:500;line-height:26px}
.step-text{position:absolute;left:440px;width:312px;text-align:center;font-size:11.5px;line-height:22px;color:var(--muted)}
.step-link{position:absolute;left:422px;width:348px;text-align:center;font-size:12px;color:var(--teal)}
.step-icon{position:absolute;left:576px;width:40px;height:40px}
.care-panel{left:423px;top:1054px;width:349px;height:743px;background:var(--teal);color:var(--white)}
.card{position:absolute;left:441px;width:312px;border:1.5px solid var(--line);background:var(--white)}
.card-brand{position:absolute;left:0;width:100%;text-align:center;font-size:40px;color:var(--ink)}

/* right column */
.footer{left:846px;top:1890px;width:349px;height:1793px;background:var(--aqua)}
.f-head{position:absolute;left:864px;font-size:12.5px;font-weight:700}
.f-link{position:absolute;left:864px;font-size:11px;color:#333}
</style>
</head>
<body>

<!-- ========== COLUMN 1 : MENU + HOME CONTENT ========== -->
<section class="col-menu">
  <div class="a" style="left:18px;top:10px;font-size:14px;font-weight:500">Marlow</div>
  <div class="a" style="left:308px;top:14px;font-size:16px">×</div>

  <div class="nav-row" style="top:84px;color:var(--teal)"><span>Home Care</span>
    <svg width="14" height="14" viewBox="0 0 14 14"><path d="M3 5l4 4 4-4" fill="none" stroke="#5b9690" stroke-width="1.5"/></svg></div>
  <div class="a label" style="left:18px;top:135px;font-size:11px">Our Services</div>

  <div class="menu-item" style="top:168px"><svg viewBox="0 0 18 18"><rect x="3" y="4" width="12" height="11" fill="none" stroke="#5b9690" stroke-width="1.4"/><path d="M9 7v5M6.5 9.5h5" stroke="#5b9690" stroke-width="1.4"/></svg>Nurse Aid care</div>
  <div class="menu-item" style="top:212px"><svg viewBox="0 0 18 18"><circle cx="9" cy="9" r="6" fill="none" stroke="#5b9690" stroke-width="1.4"/><path d="M9 5v4l3 2" fill="none" stroke="#5b9690" stroke-width="1.4"/></svg>24-Hour Home Care</div>
  <div class="menu-item" style="top:257px"><svg viewBox="0 0 18 18"><rect x="2" y="5" width="14" height="9" rx="2" fill="none" stroke="#5b9690" stroke-width="1.4"/><path d="M9 7v5M6.5 9.5h5" stroke="#5b9690" stroke-width="1.4"/></svg>Skilled Nursing</div>
  <div class="menu-item" style="top:301px"><svg viewBox="0 0 18 18"><path d="M9 2v14M2 9h14" stroke="#5b9690" stroke-width="1.4"/></svg>Lifestyle Aid</div>
  <div class="menu-item" style="top:346px"><svg viewBox="0 0 18 18"><path d="M3 9l6-5 6 5v6H3z" fill="none" stroke="#5b9690" stroke-width="1.4"/></svg>Hospice at Home</div>
  <div class="menu-item" style="top:391px"><svg viewBox="0 0 18 18"><circle cx="9" cy="5" r="3" fill="none" stroke="#5b9690" stroke-width="1.4"/><path d="M4 16c0-4 2-6 5-6s5 2 5 6" fill="none" stroke="#5b9690" stroke-width="1.4"/></svg>Bathing and Meal Service</div>

  <div class="a product-panel"></div>
  <div class="a label" style="left:40px;top:458px;font-size:11px">Product</div>
  <div class="a brand-box">Marlow Homecare</div>
  <div class="a teal" style="left:40px;top:697px;font-size:12px">Marlow Homecare</div>
  <div class="a" style="left:40px;top:721px;width:250px;font-size:11px;line-height:19px;color:#333">provides a variety of professional in-home health care services</div>
  <div class="a link" style="left:40px;top:788px;text-decoration:underline">Learn more &nbsp;›</div>

  <div class="nav-row" style="top:848px"><span>Senior Living</span><span>›</span></div>
  <div class="nav-row" style="top:895px"><span>Rates</span></div>
  <div class="nav-row" style="top:943px"><span>About Us</span><span>›</span></div>

  <div class="btn btn-line" style="left:18px;top:1019px;width:312px;height:38px">Join</div>
  <div class="btn btn-fill" style="left:18px;top:1072px;width:312px;height:36px">Learn More</div>

  <h1 class="a" style="left:18px;top:1302px;width:300px;font-size:36px;line-height:44px">Compassionate Care for Your Loved Ones</h1>
  <p class="a small" style="left:18px;top:1455px;width:310px">At our home care services, we prioritize the well-being and comfort of your family members. Experience the warmth and dedication of our compassionate caregivers who are here to support every step of the way.</p>
  <div class="a" style="left:18px;top:1586px;width:280px;height:48px;border:1.5px solid var(--line);font-size:12px;color:#aaa;padding:15px 12px">Enter Zip Code</div>
  <div class="btn btn-fill" style="left:18px;top:1645px;width:142px;height:45px">Find Comunity</div>

  <h2 class="a" style="left:18px;top:1816px;width:300px;font-size:28px;line-height:35px">Provide The Best Service For You</h2>
  <div class="photo" role="img" aria-label="Caregiver walking outdoors with an older woman using a walker" style="left:18px;top:1926px;width:312px;height:202px"></div>
  <div class="photo" role="img" aria-label="Nurse assisting an elderly man seated on his bed" style="left:18px;top:2165px;width:312px;height:189px;background:linear-gradient(135deg,#c9b45a,#5b9ab4)"></div>
  <div class="btn btn-fill" style="left:18px;top:2388px;width:312px;height:47px">See Details</div>

  <h2 class="a" style="left:18px;top:2514px;width:310px;font-size:28px;line-height:35px">Discover Exceptional Home Care Tailored to Your Loved Ones' Needs</h2>
  <p class="a small" style="left:18px;top:2674px;width:312px">Our home care services provide personalized support in the comfort of your home. Experience compassionate care that prioritizes your loved one's well-being.</p>
  <div class="a label" style="left:18px;top:2797px;font-size:13px">Personalized Care</div>
  <p class="a small" style="left:18px;top:2829px;width:312px">We create customized care plans that cater to individual needs and preferences.</p>
  <div class="a label" style="left:18px;top:2898px;font-size:13px">Trained Professionals</div>
  <p class="a small" style="left:18px;top:2930px;width:312px">Our caregivers are skilled, compassionate, and dedicated to enhancing quality of life.</p>

  <div class="a" style="left:18px;top:3090px;font-size:11px">Compassion</div>
  <h2 class="a" style="left:18px;top:3118px;width:300px;font-size:32px;line-height:39px">Exceptional Care in a Home-Like Environment</h2>
  <p class="a small" style="left:18px;top:3258px;width:312px">Our adult residential home care services provide personalized support tailored to each individual's needs. Experience a nurturing atmosphere that promotes independence and well-being.</p>
  <div class="btn btn-fill" style="left:18px;top:3390px;width:113px;height:37px">Learn More</div>
  <div class="btn btn-line" style="left:143px;top:3390px;width:114px;height:37px">Join</div>
  <div class="photo" role="img" aria-label="Residents and caregivers gathered in a bright living room" style="left:18px;top:3472px;width:312px;height:211px;background:linear-gradient(135deg,#d6b052,#7d8c5a)"></div>
</section>

<!-- ========== COLUMN 2 : STEPS + PRODUCTS ========== -->
<section class="col-steps">
  <h2 class="a center" style="left:430px;top:24px;width:332px;font-size:29px;line-height:35px">Discover How Our Care Services Transform Lives, One Step at a Time</h2>

  <svg class="step-icon" style="top:214px" viewBox="0 0 40 40"><g stroke="#5b9690" stroke-width="2.5" stroke-linecap="round"><path d="M20 4v8M20 28v8M4 20h8M28 20h8M9 9l5 5M26 26l5 5M9 31l5-5M26 14l5-5"/></g></svg>
  <div class="step-title" style="top:276px">Begin Your Journey to Compassionate Care and Support Today</div>
  <div class="step-text" style="top:371px">Getting started with our services is simple and tailored to your needs.</div>
  <div class="step-link" style="top:440px">Start &nbsp;›</div>

  <svg class="step-icon" style="top:508px" viewBox="0 0 40 40"><rect x="5" y="8" width="30" height="26" fill="none" stroke="#5b9690" stroke-width="2"/><path d="M5 15h30M12 4v7M28 4v7M13 24l4 4 8-8" fill="none" stroke="#5b9690" stroke-width="2"/></svg>
  <div class="step-title" style="top:569px">Step 1: Schedule a Free Consultation to Discuss Your Care Needs</div>
  <div class="step-text" style="top:638px">Our team will assess your situation and recommend personalized care options.</div>
  <div class="step-link" style="top:708px">Consult &nbsp;›</div>

  <svg class="step-icon" style="top:776px" viewBox="0 0 40 40"><path d="M8 30l4-12 14-12 8 8-12 14z" fill="none" stroke="#5b9690" stroke-width="2"/><path d="M8 30l10-4" stroke="#5b9690" stroke-width="2"/></svg>
  <div class="step-title" style="top:836px">Step 2: Create a Customized Care Plan That Fits Your Lifestyle</div>
  <div class="step-text" style="top:906px">We collaborate with you to design a plan that meets your goals.</div>
  <div class="step-link" style="top:975px">Plan &nbsp;›</div>

  <div class="a care-panel"></div>
  <div class="a" style="left:441px;top:1117px;font-size:11px;color:var(--white)">Care</div>
  <h2 class="a" style="left:441px;top:1148px;width:300px;font-size:32px;line-height:40px;color:var(--white)">Discover the Benefits of Home Care Services</h2>
  <p class="a" style="left:441px;top:1285px;width:314px;font-size:11.5px;line-height:22px;color:#eaf5f3">Choosing our home care services ensures personalized support tailored to your loved one's needs. Enjoy peace of mind knowing they are in a safe and nurturing environment.</p>
  <div class="btn" style="left:441px;top:1396px;width:123px;height:44px;border:1.5px solid var(--white);color:var(--white)">Learn More</div>
  <div class="a" style="left:584px;top:1410px;font-size:12px;color:var(--white)">Get Started &nbsp;›</div>
  <div class="a" style="left:500px;top:1489px;width:250px;height:245px;background:var(--teal-soft)"></div>
  <div class="photo" role="img" aria-label="Caregiver serving a meal to an older woman at home" style="left:441px;top:1509px;width:279px;height:206px;background:linear-gradient(135deg,#8a3a22,#d2c07a)"></div>

  <div class="a center" style="left:422px;top:1860px;width:348px;font-size:11px;font-weight:500">Product</div>
  <h2 class="a center" style="left:432px;top:1894px;width:328px;font-size:34px;line-height:43px">Find The Right Service For Your Beloved Ones</h2>
  <p class="a center" style="left:440px;top:2050px;width:312px;font-size:13px;line-height:22px;color:#333">Lorem ipsum dolor sit amet, consectetur adipiscing elit.</p>

  <div class="card" style="top:2172px;height:534px"></div>
  <div class="photo" role="img" aria-label="Caregivers doing light exercise with seniors" style="left:442px;top:2173px;width:310px;height:188px;background:linear-gradient(135deg,#3f6fa8,#c9a067)"></div>
  <div class="a" style="left:441px;top:2384px;font-size:11px">Tagline</div>
  <h3 class="a" style="left:441px;top:2409px;width:310px;font-size:32px;line-height:44px">Discover Benefits of Our Products</h3>
  <p class="a small" style="left:441px;top:2519px;width:306px">Choosing the right from our products ensure personalized support tailored to your loved ones. Enjoy peace of knowing they are in safe and nurturing environment</p>
  <div class="btn btn-fill" style="left:441px;top:2639px;width:112px;height:38px">Learn More</div>
  <div class="btn btn-line" style="left:566px;top:2639px;width:114px;height:38px">Join</div>

  <div class="card" style="top:2732px;height:531px"></div>
  <div class="card-brand" style="left:441px;width:312px;top:2812px;font-size:34px">Marlow Homecare</div>
  <div class="a" style="left:464px;top:2967px;font-size:11px">Product</div>
  <h3 class="a" style="left:464px;top:2993px;width:270px;font-size:21px;line-height:32px">Professional Care In Your Home</h3>
  <p class="a small" style="left:464px;top:3063px;width:270px">Every person's care journey is unique. We tailor our in-home services to meet the diverse nurturing experience of professional quality care and safety within the comfort and convenience of your own home.</p>
  <div class="a link" style="left:464px;top:3222px">See More &nbsp;›</div>

  <div class="card" style="top:3292px;height:502px"></div>
  <div class="card-brand" style="left:441px;width:312px;top:3376px;font-size:30px">Marlow Senior Living</div>
  <div class="a" style="left:464px;top:3524px;font-size:11px">Product</div>
  <h3 class="a" style="left:464px;top:3553px;width:270px;font-size:21px;line-height:32px">Trusted Care In Our Home</h3>
  <p class="a small" style="left:464px;top:3591px;width:270px">Creates a warm, supportive, and enriching care home environment where seniors can thrive in their golden years. We provide residential care that promotes well-being, connection, and dignity of each individual</p>
  <div class="a link" style="left:464px;top:3749px">Button &nbsp;›</div>
</section>

<!-- ========== COLUMN 3 : TESTIMONIAL + CAREER + FOOTER ========== -->
<section class="col-right">
  <div class="a center" style="left:846px;top:54px;width:346px;font-size:12px;font-weight:500">In Partnership With</div>
  <div class="a" style="left:958px;top:132px;display:flex;align-items:center;gap:10px;font-size:22px;font-weight:500">
    <span style="width:22px;height:22px;background:var(--ink);display:inline-block"></span>Lumenro</div>

  <div class="a" role="img" aria-label="Portrait of a smiling older man reading a newspaper" style="left:864px;top:334px;width:312px;height:312px;border-radius:50%;background:radial-gradient(circle at 40% 40%,#b5a99a,#8a3a1f)"></div>

  <svg class="a" style="left:864px;top:750px" width="110" height="20" viewBox="0 0 110 20"><g fill="#141414"><path id="st" d="M10 1l2.6 6 6.4.6-4.9 4.2 1.5 6.3L10 14.8 4.4 18.1l1.5-6.3L1 7.6l6.4-.6z"/><use href="#st" x="22"/><use href="#st" x="44"/><use href="#st" x="66"/><use href="#st" x="88"/></g></svg>
  <p class="a" style="left:864px;top:797px;width:318px;font-size:17px;line-height:24px;font-weight:500">"The care my mother received was exceptional. The staff treated her like family, and I couldn't be more grateful."</p>
  <div class="a" style="left:864px;top:955px;width:52px;height:52px;border-radius:50%;background:#e3e3e3"></div>
  <div class="a" style="left:864px;top:1027px;font-size:12px;font-weight:500">Clara Nguyen</div>
  <div class="a" style="left:864px;top:1049px;font-size:12px;color:#444">Daughter, Happy Home</div>
  <div class="a" style="left:864px;top:1087px;width:153px;height:1px;background:var(--ink)"></div>
  <div class="a" style="left:864px;top:1117px;display:flex;align-items:center;gap:6px;font-size:17px;font-weight:500">
    <span style="width:16px;height:16px;background:var(--ink);display:inline-block"></span>Weavel</div>

  <div class="a" style="left:864px;top:1275px;font-size:18px;font-weight:500">Career</div>
  <h2 class="a" style="left:864px;top:1322px;font-size:40px;font-weight:500">Job Opening</h2>
  <p class="a small" style="left:864px;top:1400px;width:320px;font-size:13px;color:#333">Explore rewarding career opportunities in home care and adult residential support</p>
  <div class="btn btn-fill" style="left:864px;top:1479px;width:131px;height:46px">Explore Job</div>
  <div class="a" role="img" aria-label="Illustration of a caregiver helping an older man with a walker" style="left:883px;top:1552px;width:260px;height:275px;background:linear-gradient(160deg,#eef4f4,#cfe3e1 60%,#7aa7a3)"></div>

  <div class="a footer"></div>
  <div class="a" style="left:864px;top:1950px;display:flex;gap:14px;font-size:14px;font-weight:500">
    <span>Marlow</span><span>Marlow Homecare</span></div>
  <div class="a" style="left:864px;top:1972px;font-size:12px;color:#555">Marlow Senior Living</div>

  <div class="f-head" style="top:2034px">Address:</div>
  <div class="f-link" style="top:2065px">248 Pueo Lane, Suite 310, Honolulu, HI 96817</div>
  <div class="f-head" style="top:2107px">Contact:</div>
  <div class="f-link" style="top:2140px">808-555-0172</div>

  <div class="f-head" style="top:2196px">Quick Links</div>
  <div class="f-link" style="top:2239px">Nurse Aide Care</div>
  <div class="f-link" style="top:2273px">24-Hour Home Care</div>
  <div class="f-link" style="top:2307px">Skilled Nursing</div>
  <div class="f-link" style="top:2341px">Lifestyle Aide</div>
  <div class="f-link" style="top:2375px">Hospice at Home</div>
  <div class="f-link" style="top:2409px">Bathing &amp; Meal Service</div>

  <div class="f-head" style="top:2475px">Resources</div>
  <div class="f-link" style="top:2520px">Learn</div>
  <div class="f-link" style="top:2554px">Testimonials</div>
  <div class="f-link" style="top:2588px">Caregiver Jobs</div>
  <div class="f-link" style="top:2622px">Guides</div>
  <div class="f-link" style="top:2656px">Community</div>

  <div class="f-head" style="top:2722px">Stay Connected</div>
  <div class="f-link" style="top:2762px">Friendbook</div>
  <div class="f-link" style="top:2796px">Chirper</div>
  <div class="f-link" style="top:2830px">WorkLink</div>
  <div class="f-link" style="top:2864px">Snapgram</div>
  <div class="f-link" style="top:2898px">ViewTube</div>

  <div class="a" style="left:864px;top:2967px;width:312px;height:1px;background:#333"></div>
  <div class="a" style="left:864px;top:2992px;display:flex;gap:16px">
    <span style="width:17px;height:17px;border-radius:50%;background:var(--ink)"></span>
    <span style="width:17px;height:17px;border-radius:50%;background:var(--ink)"></span>
    <span style="width:17px;height:17px;border-radius:50%;background:var(--ink)"></span>
    <span style="width:17px;height:17px;border-radius:50%;background:var(--ink)"></span>
    <span style="width:17px;height:17px;border-radius:50%;background:var(--ink)"></span>
  </div>
  <div class="f-link" style="top:3044px;text-decoration:underline">Privacy Policy</div>
  <div class="f-link" style="top:3078px;text-decoration:underline">Terms of Service</div>
  <div class="f-link" style="top:3112px;text-decoration:underline">Cookies Settings</div>
  <div class="f-link" style="top:3163px">© 2024 Lumenro. All rights reserved.</div>
</section>

</body>
</html>
```